Business cards to launch an education platform

Hi,
I am looking at having new business cards designed.
I am a startup, developing a web platform for schools and university, the education world. It's an online assessment system.
I would like a card that looks classy, and that is using the colors and the font of my logo.

I have attached:
1) my logo
2) A business card that I have designed quickly so you can have all the information required in the card, but I really don't like it.
3) The font that I am using (Lato Regular) to design my web platform
4) Some screenshots of my web platform so you can have a look at the style that I have.

Target Market(s)

Major market: Education system: Schools and university
Minor markets: Business in general

Industry/Entity Type

Business

Contact Information for Business Card

Clara Fenwick
Director

M: 0437 518 902
E: clara.fenwick@amberLoomSystems.com.au

Requirements
Must have
• The colors of my logo

```html
<!DOCTYPE html>
<html lang="en">
<head>
<meta charset="utf-8">
<title>Amber Loom Systems – Business Cards</title>
<link rel="stylesheet" href="https://fonts.googleapis.com/css2?family=Open+Sans:wght@400;600&display=swap">
<style>
  :root {
    --backdrop: #d8dadd;
    --card-white: #f2f3f5;
    --navy: #0f3b6c;
    --sky: #2b9fd8;
    --ink: #3f4347;
    --rule: #7f94a8;
    --white: #f4f6f8;
  }
  * { margin: 0; padding: 0; box-sizing: border-box; }
  html, body {
    width: 1105px;
    height: 1200px;
    overflow: hidden;
    background: var(--backdrop);
    font-family: "Open Sans", Arial, sans-serif;
  }
  .canvas {
    position: relative;
    width: 1105px;
    height: 1200px;
  }
  .card {
    position: absolute;
    left: 182px;
    width: 747px;
    height: 427px;
  }
  .card--front { top: 119px; background: var(--card-white); }
  .card--back  { top: 637px; background: var(--navy); }

  .brand {
    position: absolute;
    left: 500px;
    top: 60px;
    width: 200px;
    text-align: center;
    color: var(--navy);
    font-weight: 400;
    line-height: 1.15;
  }
  .brand__mark {
    display: block;
    width: 57px;
    height: 57px;
    margin: 0 auto 14px;
    background: var(--navy);
  }
  .brand__name { font-size: 30px; letter-spacing: 1.5px; }
  .brand__sub { font-size: 22px; letter-spacing: 1px; }

  .holder {
    position: absolute;
    left: 48px;
    top: 306px;
    font-size: 27px;
    font-weight: 600;
    color: var(--navy);
  }
  .holder__role {
    font-size: 20px;
    font-weight: 400;
    color: var(--sky);
  }
  .rule {
    position: absolute;
    left: 48px;
    top: 350px;
    width: 649px;
    height: 2px;
    background: var(--rule);
  }
  .contacts {
    position: absolute;
    left: 48px;
    top: 360px;
    display: flex;
    align-items: center;
    gap: 10px;
    font-size: 19.5px;
    color: var(--ink);
  }
  .contacts svg { display: block; }
  .contacts__divider { margin: 0 2px; }

  .back-brand {
    position: absolute;
    left: 440px;
    top: 225px;
    width: 290px;
    text-align: center;
    color: var(--white);
    font-size: 30px;
    font-weight: 400;
    line-height: 1.15;
    letter-spacing: 1px;
  }
  .web {
    position: absolute;
    left: 440px;
    top: 360px;
    width: 290px;
    text-align: center;
    color: var(--white);
    font-size: 19.5px;
  }
</style>
</head>
<body>
<main class="canvas">
  <section class="card card--front" aria-label="Business card front">
    <div class="brand">
      <span class="brand__mark"></span>
      <div class="brand__name">AMBER LOOM</div>
      <div class="brand__sub">Systems</div>
    </div>
    <p class="holder">Clara Fenwick - <span class="holder__role">Director</span></p>
    <div class="rule"></div>
    <div class="contacts">
      <svg width="14" height="22" viewBox="0 0 14 22" aria-hidden="true">
        <rect x="1" y="1" width="12" height="20" rx="2" fill="none" stroke="#0f3b6c" stroke-width="2"/>
        <rect x="3.5" y="4" width="7" height="11" fill="#0f3b6c"/>
        <circle cx="7" cy="18" r="1.2" fill="#0f3b6c"/>
      </svg>
      <span>0437 518 902</span>
      <span class="contacts__divider">|</span>
      <svg width="20" height="14" viewBox="0 0 20 14" aria-hidden="true">
        <rect x="0" y="0" width="20" height="14" rx="1" fill="#0f3b6c"/>
        <path d="M1 1 L10 8 L19 1" fill="none" stroke="#f2f3f5" stroke-width="1.6"/>
      </svg>
      <span>clara.fenwick@amberLoomSystems.com.au</span>
    </div>
  </section>

  <section class="card card--back" aria-label="Business card back">
    <div class="back-brand">AMBER LOOM<br>Systems</div>
    <p class="web">amberLoomSystems.com.au</p>
  </section>
</main>
</body>
</html>
```